4th Generation Family Business Needs a New Card Design!

We are a family owned 4th Generation company. We are based in the Sydney, Australia area and we are desperately in need of a more modern and classy card. We are monumental masons who design, supply & erect lasting memorials throughout cemeteries in Sydney. Our customers are normally in a period of grieving. I have attached logo files that will need to be implemented on the card. Company was established 1935. Australian Owned and Operated. Card needs to be designed to PIXO.com specification.

Target Market(s)

Our target market is based upon people that a grieving for family members that have passed away. We also deal with alot of companies that own and operate cemeteries.

Industry/Entity Type

Business

Contact Information for Business Card

Simon Harcourt, Operations Manager, 0417293086, simon@harcourtmemorials.com.au
Lewis Harcourt, Director, 0491630572, lewis@harcourtmemorials.com.au
Phone # 02 9561 3048
Website: www.harcourtmemorials.com.au
Address: Suite 17, 8 Palfrey Lane, West Carlow, Sydney NSW 2156

Font styles to use
Serif
Decorative
Script

Requirements
Must have
• Would like to see the logo nicely implemented with a modern design. Embossed lettering would be a nice additive.

```html
<!DOCTYPE html>
<html lang="en">
<head>
<meta charset="utf-8">
<title>Harcourt Memorials – Business Card</title>
<link href="https://fonts.googleapis.com/css2?family=EB+Garamond:wght@400;500;600&family=Cinzel:wght@400&display=swap" rel="stylesheet">
<style>
  :root {
    --backdrop: #e9eaec;
    --card-white: #ffffff;
    --card-black: #231f20;
    --ink: #1f1c1d;
    --ink-soft: #55504f;
    --gold: #e8b92c;
    --rule: #3a3536;
  }
  * { margin: 0; padding: 0; box-sizing: border-box; }
  html, body {
    width: 1200px; height: 1200px; overflow: hidden;
    background: var(--backdrop);
    font-family: "EB Garamond", Georgia, serif;
  }
  .sheet {
    width: 1200px; height: 1200px;
    display: flex; flex-direction: column; align-items: center; justify-content: center;
    gap: 60px;
  }
  .card {
    position: relative;
    width: 820px; height: 500px;
    box-shadow: 0 8px 24px rgba(0,0,0,0.18);
    overflow: hidden;
  }

  /* Back of card */
  .card--back { background: var(--card-black); }
  .back-brand {
    position: absolute; left: 0; right: 0; top: 170px;
    text-align: center;
    font-family: "Cinzel", "EB Garamond", serif;
    font-size: 46px; letter-spacing: 4px;
    color: var(--card-white);
  }
  .back-rule {
    position: absolute; left: 40px; right: 40px; top: 330px;
    height: 1px; background: var(--gold);
  }
  .back-web {
    position: absolute; right: 48px; top: 345px;
    font-size: 26px; letter-spacing: 6px;
    color: var(--card-white);
  }
  .back-web .accent { color: var(--gold); }

  /* Front of card */
  .card--front { background: var(--card-white); }
  .holder { position: absolute; left: 56px; top: 48px; }
  .holder-name {
    font-size: 44px; font-weight: 600; color: var(--ink); line-height: 1;
  }
  .holder-name .surname { color: var(--gold); }
  .holder-title {
    margin-top: 8px; font-size: 24px; color: var(--ink-soft);
  }
  .front-brand {
    position: absolute; left: 40px; top: 330px; width: 360px;
    text-align: center;
    font-family: "Cinzel", "EB Garamond", serif;
    font-size: 38px; line-height: 1.15; letter-spacing: 2px;
    color: var(--ink);
  }
  .divider {
    position: absolute; left: 420px; top: 270px;
    width: 1px; height: 200px; background: var(--rule);
  }
  .contact { position: absolute; left: 446px; top: 268px; }
  .contact-row {
    font-size: 24px; line-height: 34px; color: var(--ink);
  }
  .contact-label {
    display: inline-block; width: 34px; color: var(--gold);
  }
  .address {
    margin-top: 18px; font-size: 24px; line-height: 30px; color: var(--ink);
  }
</style>
</head>
<body>
<main class="sheet">
  <section class="card card--back" aria-label="Card back">
    <div class="back-brand">HARCOURT MEMORIALS</div>
    <div class="back-rule"></div>
    <div class="back-web">www.<span class="accent">harcourtmemorials</span>.com.au</div>
  </section>

  <section class="card card--front" aria-label="Card front">
    <div class="holder">
      <div class="holder-name">Simon <span class="surname">Harcourt</span></div>
      <div class="holder-title">Operations Manager</div>
    </div>

    <div class="front-brand">HARCOURT<br>MEMORIALS</div>

    <div class="divider"></div>

    <div class="contact">
      <div class="contact-row"><span class="contact-label">M :</span> 0417293086</div>
      <div class="contact-row"><span class="contact-label">P :</span> 02 9561 3048</div>
      <div class="contact-row"><span class="contact-label">W :</span> www.harcourtmemorials.com.au</div>
      <div class="contact-row"><span class="contact-label">E :</span> simon@harcourtmemorials.com.au</div>
      <div class="address">Suite 17, 8 Palfrey Lane<br>West Carlow, Sydney NSW 2156</div>
    </div>
  </section>
</main>
</body>
</html>
```